LoopVane - A ride hailing server VAR

our Brindle.co profile: https://brindle.co/517loopvane

LOOPVANE offers first world solutions to first world problems. These days, our smartphones are our cameras, our wallets and our ride home. LOOPVANE guarantees that even if your phone is lost or dies, you'll never get stranded again. Simply call or text (SMS) our toll-free number to request a ride, and choose from one of the various services you subscribe to. LOOPVANE verifies your identity through a unique pin, making it possible to request rides through your own account from a stranger's phone via text or phone call. You can also login through our website or our App, making it easier than ever to get home phoneless.

LOOPVANE is a heterogeneous ride-hailing service that allows users for request transportation from any "transportation network company," taxi, helicopter service, jet service or any transportation service company that is publicly available. LOOPVANE will allow users to connect through our site, automated phone system, App or any appropriated touch point available.

Target Market(s)

RIde Haling

Coding

Coded - Design and coding required

Number of Pages Required

4 page

Requirements
Must have
• hav
Nice to have
• e the same functionality as our competitor's site: https://hopquill.com/
Should not have
• should not be cheezy
• We need to have the registration/sign up on the main page like https://www.zarvix.com/

```html
<!DOCTYPE html>
<html lang="en">
<head>
<meta charset="utf-8">
<title>LOOPVANE</title>
<link href="https://fonts.googleapis.com/css2?family=Fira+Sans:wght@400;500;600;700&display=swap" rel="stylesheet">
<style>
:root{
  --yellow:#f7b500;
  --yellow-light:#ffcc1a;
  --ink:#222222;
  --text:#444444;
  --muted:#666666;
  --band:#f5f5f5;
  --white:#ffffff;
  --hero-dark:#3a2a1e;
  --hero-mid:#6e5440;
}
*{margin:0;padding:0;box-sizing:border-box}
html,body{width:792px;height:1200px;overflow:hidden;background:var(--white)}
body{font-family:"Fira Sans",Arial,sans-serif;color:var(--text);position:relative}
.abs{position:absolute}
.btn{position:absolute;background:linear-gradient(var(--yellow-light),var(--yellow));color:var(--ink);font-weight:600;font-size:7.5px;letter-spacing:.3px;display:flex;align-items:center;justify-content:center;text-transform:uppercase}

.hero{position:absolute;left:0;top:0;width:792px;height:405px;
  background:radial-gradient(ellipse at 50% 40%,var(--hero-mid),var(--hero-dark) 75%)}
.brand-mark{position:absolute;width:38px;height:38px;border-radius:4px;background:var(--yellow)}
.brand-name{position:absolute;font-weight:600;font-size:14px;letter-spacing:.3px}
.hero .brand-name{color:var(--white)}
.nav a{position:absolute;top:29px;color:var(--white);font-size:7.5px;font-weight:500;text-decoration:none;letter-spacing:.3px}
.nav .active::after{content:"";position:absolute;left:0;right:0;top:13px;height:2px;background:var(--yellow)}
.service-icon{position:absolute;border-radius:8px}
.service-label{position:absolute;top:236px;width:120px;text-align:center;color:var(--white);font-weight:600;font-size:10px}
.tagline{position:absolute;top:301px;left:0;width:792px;text-align:center;color:var(--white);font-size:11px}

.about{position:absolute;left:0;top:405px;width:792px;height:295px;background:var(--band)}
.section-title{position:absolute;left:0;width:792px;text-align:center;font-weight:600;font-size:15px;color:var(--ink);letter-spacing:.3px}
.rule{position:absolute;left:382px;width:28px;height:2px;background:var(--yellow)}
.about-copy{position:absolute;left:192px;top:110px;width:408px;text-align:center;font-size:7.4px;line-height:13.2px;color:var(--text)}

.founders{position:absolute;left:0;top:700px;width:792px;height:317px;background:var(--white)}
.founder{position:absolute;top:114px;width:150px}
.founder .photo{width:56px;height:56px;background:linear-gradient(135deg,#8a6a50,#3d2c22)}
.founder .name{margin-top:16px;color:var(--yellow);font-weight:600;font-size:10px}
.founder .role{margin-top:3px;font-weight:600;font-size:7px;color:var(--ink)}
.founder .bio{margin-top:10px;font-size:5.6px;line-height:10px;color:var(--muted)}

.partners{position:absolute;left:0;top:1017px;width:792px;height:102px;background:var(--band)}
.partner{position:absolute;top:36px;font-weight:700;font-size:26px;color:var(--ink);letter-spacing:1px}

.footer{position:absolute;left:0;top:1119px;width:792px;height:81px;background:var(--white)}
.footer .brand-name{color:var(--ink)}
.connect{position:absolute;left:284px;top:35px;font-size:4.6px;font-weight:600;color:var(--ink);text-transform:uppercase}
.social{position:absolute;top:34px;font-size:5px;font-weight:600;color:var(--ink)}
.legal{position:absolute;left:542px;top:34px;font-size:5.4px;color:var(--ink);text-transform:uppercase}
</style>
</head>
<body>

<header class="hero" role="img" aria-label="Blurred photo of hands holding a smartphone">
</header>
<div class="brand-mark" style="left:166px;top:14px"></div>
<div class="brand-name" style="left:213px;top:25px;color:var(--white)">LOOPVANE</div>
<nav class="nav">
  <a class="active" style="left:370px">HOME</a>
  <a style="left:410px">ABOUT</a>
  <a style="left:453px">SUPPORT</a>
  <a style="left:513px">CONTACT</a>
</nav>
<div class="btn" style="left:564px;top:22px;width:66px;height:23px">Sign up</div>

<div class="service-icon" role="img" aria-label="Taxi icon" style="left:192px;top:172px;width:94px;height:36px;background:var(--white)"></div>
<div class="service-icon" role="img" aria-label="Helicopter icon" style="left:350px;top:170px;width:92px;height:40px;background:var(--yellow)"></div>
<div class="service-icon" role="img" aria-label="Jet icon" style="left:529px;top:150px;width:54px;height:80px;background:var(--yellow)"></div>
<div class="service-label" style="left:175px">TAXI</div>
<div class="service-label" style="left:336px">HELICOPTER</div>
<div class="service-label" style="left:495px">JET</div>
<p class="tagline">We offers first world solutions to first world problems.</p>
<div class="btn" style="left:346px;top:326px;width:100px;height:23px">Sign up today !</div>

<section class="about">
  <h2 class="section-title" style="top:47px">ABOUT US</h2>
  <div class="rule" style="top:80px"></div>
  <p class="about-copy">LOOPVANE offers first world solutions to first world problems. These days, our smartphones are our cameras, our wallets and our ride home. LOOPVANE guarantees that even if your phone is lost or dies, you'll never get stranded again. Simply call or text (SMS) our toll-free number to request a ride, and choose from one of the various servicesyou subscribe to. LOOPVANE verifies your identity through a unique pin, making it possible to request rides through your own account from a stranger's phone via text or phone call.You can also login through our website or our App, making it easier than ever to get home phoneless.</p>
  <div class="btn" style="left:363px;top:211px;width:66px;height:23px">Read more</div>
</section>

<section class="founders">
  <h2 class="section-title" style="top:42px">FOUNDERS</h2>
  <div class="rule" style="top:75px"></div>
  <div class="founder" style="left:161px">
    <div class="photo" role="img" aria-label="Portrait photo of the CEO"></div>
    <div class="name">DORIAN VELL</div>
    <div class="role">CEO</div>
    <p class="bio">Founder @Quarrow.org, @517LOOPVANE • Worked at @Pelmont, @Ostrand Sound Group</p>
  </div>
  <div class="founder" style="left:322px">
    <div class="photo" role="img" aria-label="Portrait photo of the CMO"></div>
    <div class="name">TESSA MARLOW</div>
    <div class="role">CMO</div>
    <p class="bio">Social Media Coordinator, Marketer, Product Development, Copywriter/Content Creator</p>
  </div>
  <div class="founder" style="left:482px">
    <div class="photo" role="img" aria-label="Portrait photo of the CFO"></div>
    <div class="name">IRENE K. SOMA</div>
    <div class="role">CFO</div>
    <p class="bio">Experienced building and leading teams to solve business challenges.</p>
  </div>
</section>

<section class="partners">
  <span class="partner" style="left:196px;letter-spacing:4px">ZARVIX</span>
  <span class="partner" style="left:356px">Carrow</span>
  <span class="partner" style="left:522px">Mapley</span>
</section>

<footer class="footer">
  <div class="brand-mark" style="left:166px;top:18px"></div>
  <div class="brand-name" style="left:213px;top:29px">LOOPVANE</div>
  <span class="connect">Connect with us</span>
  <span class="social" style="left:332px">Faceline</span>
  <span class="social" style="left:355px">Chirrup</span>
  <span class="social" style="left:377px">Vidloom</span>
  <span class="legal">Terms of use &nbsp;| Privacy policy</span>
</footer>

</body>
</html>
```